Dunmore Roofing

Want a professional looking business card

Industry/Entity Type

Business

Contact Information for Business Card

Paul Dunmore ( Owner) paul@dunmoreroofing-example.com, www.dunmoreroofing-example.com, Adress: 4172 Township road 43 Ashvale,NR K9X4T2

```html
<!DOCTYPE html>
<html lang="en">
<head>
<meta charset="utf-8">
<title>Dunmore Roofing – Business Card</title>
<link href="https://fonts.googleapis.com/css2?family=Open+Sans:wght@400;600;700&display=swap" rel="stylesheet">
<style>
  :root {
    --stage: #000000;
    --card-light: #f3f3f3;
    --brand-blue: #1e4a8a;
    --brand-blue-soft: #2a5596;
    --ink: #333333;
    --ink-muted: #555555;
    --white: #ffffff;
  }
  * { margin: 0; padding: 0; box-sizing: border-box; }
  html, body {
    width: 1200px; height: 900px; overflow: hidden;
    background: var(--stage);
    font-family: "Open Sans", Arial, sans-serif;
  }
  .canvas { position: relative; width: 1200px; height: 900px; }

  .card {
    position: absolute; top: 200px; width: 310px; height: 502px; overflow: hidden;
  }
  .card--front {
    left: 265px; background: var(--card-light);
    border-radius: 72px 0 72px 0;
  }
  .card--back {
    left: 641px; background: var(--brand-blue);
    border-radius: 0 72px 0 72px;
  }

  .brand-name {
    position: absolute; left: 0; width: 100%; text-align: center;
    font-weight: 700; color: var(--brand-blue); line-height: 1.1;
  }
  .brand-name__main { font-size: 32px; letter-spacing: 2px; }
  .brand-name__sub { font-size: 17px; letter-spacing: 11px; padding-left: 11px; }
  .card--front .brand-name { top: 150px; }
  .card--back .brand-name { top: 225px; color: var(--white); }
  .card--back .brand-name__main { font-size: 34px; }
  .card--back .brand-name__sub { font-size: 18px; }
  .brand-mark {
    display: inline-block; width: 10px; height: 10px; background: currentColor;
    vertical-align: middle; margin-top: -3px;
  }

  .contact { position: absolute; left: 26px; top: 329px; color: var(--ink); font-size: 13.5px; line-height: 18px; }
  .contact__name { color: var(--brand-blue); font-size: 17px; font-weight: 600; line-height: 20px; }
  .contact__role { color: var(--ink-muted); font-size: 13.5px; }
  .contact__address { margin-top: 12px; }
  .contact__links { margin-top: 14px; list-style: none; }
  .contact__links li { display: flex; align-items: center; gap: 6px; }
  .contact__links svg { width: 11px; height: 11px; flex: none; }

  .back-gloss {
    position: absolute; left: 0; top: 0; width: 100%; height: 22px;
    background: var(--brand-blue-soft);
  }
  .back-decoration {
    position: absolute; left: 0; top: 150px; width: 310px; height: 270px;
  }
</style>
</head>
<body>
<main class="canvas">
  <section class="card card--front" aria-label="Business card front">
    <div class="brand-name">
      <div class="brand-name__main">DUNMORE</div>
      <div class="brand-name__sub">ROOFING<span class="brand-mark"></span></div>
    </div>
    <div class="contact">
      <p class="contact__name">PAUL DUNMORE</p>
      <p class="contact__role">Owner</p>
      <p class="contact__address">4172 Township road 43<br>Ashvale,NR K9X4T2</p>
      <ul class="contact__links">
        <li>
          <svg viewBox="0 0 12 12" aria-hidden="true"><rect x="0.5" y="2" width="11" height="8" fill="var(--brand-blue)"/><path d="M0.5 2 L6 6.5 L11.5 2" stroke="var(--card-light)" stroke-width="1.2" fill="none"/></svg>
          paul@dunmoreroofing-example.com
        </li>
        <li>
          <svg viewBox="0 0 12 12" aria-hidden="true"><circle cx="6" cy="6" r="5.5" fill="var(--brand-blue)"/></svg>
          www.dunmoreroofing-example.com
        </li>
      </ul>
    </div>
  </section>

  <section class="card card--back" aria-label="Business card back">
    <div class="back-gloss"></div>
    <svg class="back-decoration" viewBox="0 0 310 270" role="img" aria-label="Faint background decoration area">
      <defs>
        <linearGradient id="backFade" x1="0" y1="0" x2="0" y2="1">
          <stop offset="0" stop-color="#2c5797"/>
          <stop offset="1" stop-color="#1e4a8a"/>
        </linearGradient>
      </defs>
      <polygon points="0,210 105,25 310,25 310,180" fill="url(#backFade)" opacity="0.8"/>
    </svg>
    <div class="brand-name">
      <div class="brand-name__main">DUNMORE</div>
      <div class="brand-name__sub">ROOFING<span class="brand-mark"></span></div>
    </div>
  </section>
</main>
</body>
</html>
```